BUSINESS CARD DESIGN

NAME- DALE VORSKIN
PHONE NUMER - 555- 714-9082
EMAIL- OFFICE@TRV-GROUNDMAKRZ.COM
BACK OF CARD- SPEACIALIZES IN LAND CLEARING, FORESTRY MUCLHING AND EXCAVATION

Contact Information for Business Card

NAME- DALE VORSKIN PHONE NUMER - 555- 714-9082 EMAIL- OFFICE@TRV-GROUNDMAKRZ.COM BACK OF CARD- SPEACIALIZES IN LAND CLEARING , MUCLHING AND EXCAVATION

```html
<!DOCTYPE html>
<html lang="en">
<head>
<meta charset="utf-8">
<title>Traverse Ground Makrz – Business Cards</title>
<link rel="stylesheet" href="https://fonts.googleapis.com/css2?family=Michroma&family=Roboto:wght@400;500&display=swap">
<style>
  :root {
    --bg: #141414;
    --card-top: #2e2e2e;
    --card-bottom: #1e1e1e;
    --gold: #f7b611;
    --gold-deep: #f59a0c;
    --white: #f2f2f2;
    --faint: rgba(255,255,255,0.045);
    --rule: #cfcfcf;
  }
  * { margin: 0; padding: 0; box-sizing: border-box; }
  html, body { width: 1200px; height: 840px; overflow: hidden; background: var(--bg); }
  .canvas { position: relative; width: 1200px; height: 840px; }

  .card {
    position: absolute;
    width: 560px; height: 320px;
    border-radius: 22px;
    background: linear-gradient(160deg, var(--card-top), var(--card-bottom));
    border-bottom: 5px solid var(--gold-deep);
    border-left: 2px solid var(--gold);
    overflow: hidden;
    box-shadow: 0 18px 40px rgba(0,0,0,0.6);
    font-family: "Roboto", Arial, sans-serif;
  }
  .card--back { left: 50px; top: 60px; }
  .card--front { left: 590px; top: 460px; }

  .wordmark { font-family: "Michroma", Arial, sans-serif; color: var(--gold); text-align: center; line-height: 1.25; }
  .wordmark__name { font-size: 17px; letter-spacing: 1px; }
  .wordmark__sub { font-size: 9px; letter-spacing: 5px; }

  /* back */
  .emblem-faint {
    position: absolute; left: -40px; top: 40px;
    width: 330px; height: 330px; border-radius: 50%;
    background: radial-gradient(circle at 40% 40%, #3a3a3a, #222);
    box-shadow: inset 0 2px 6px rgba(255,255,255,0.08), inset 0 -4px 10px rgba(0,0,0,0.5);
  }
  .card--back .wordmark { position: absolute; right: 40px; top: 34px; }
  .wordmark__rule { height: 2px; background: var(--gold); margin: 5px auto 0; width: 80%; }
  .specialties { position: absolute; right: 40px; top: 150px; text-align: right; }
  .specialties__title { font-family: "Michroma", Arial, sans-serif; font-size: 13px; color: var(--gold); margin-bottom: 10px; }
  .specialties__list { list-style: none; }
  .specialties__list li { color: var(--white); font-size: 16px; line-height: 1.45; letter-spacing: 0.5px; }
  .specialties__list li::after {
    content: ""; display: inline-block; width: 7px; height: 7px; border-radius: 50%;
    background: var(--gold); margin-left: 8px; vertical-align: middle;
  }

  /* front */
  .card--front .emblem-faint { left: 90px; top: 70px; width: 300px; height: 300px; background: var(--faint); box-shadow: none; }
  .brand { position: absolute; right: 40px; top: 26px; display: flex; flex-direction: column; align-items: center; gap: 10px; }
  .brand__dot { width: 74px; height: 74px; border-radius: 50%; background: var(--gold); }
  .brand-rule { position: absolute; right: 30px; top: 178px; width: 300px; height: 1px; background: var(--rule); }
  .person { position: absolute; left: 36px; bottom: 78px; font-family: "Michroma", Arial, sans-serif; font-size: 24px; color: var(--gold); letter-spacing: 1px; }
  .person-rule { position: absolute; left: 36px; right: 30px; bottom: 66px; height: 1px; background: var(--rule); }
  .contact { position: absolute; left: 36px; bottom: 28px; display: flex; gap: 26px; color: var(--white); font-size: 16px; align-items: center; }
  .contact__item { display: flex; align-items: center; gap: 8px; }
  .contact__email { text-transform: lowercase; }
  .icon { width: 16px; height: 16px; fill: var(--gold); }
</style>
</head>
<body>
<main class="canvas">

  <section class="card card--back" aria-label="Card back">
    <div class="emblem-faint" aria-hidden="true"></div>
    <div class="wordmark">
      <div class="wordmark__name">TRAVERSE GROUND</div>
      <div class="wordmark__sub">MAKRZ LLC</div>
      <div class="wordmark__sub">HAWAII</div>
      <div class="wordmark__rule"></div>
    </div>
    <div class="specialties">
      <h2 class="specialties__title">SPEACIALIZES IN</h2>
      <ul class="specialties__list">
        <li>LAND CLEARING</li>
        <li>MUCLHING</li>
        <li>EXCAVATION</li>
      </ul>
    </div>
  </section>

  <section class="card card--front" aria-label="Card front">
    <div class="emblem-faint" aria-hidden="true"></div>
    <div class="brand">
      <div class="brand__dot" aria-hidden="true"></div>
      <div class="wordmark">
        <div class="wordmark__name">TRAVERSE GROUND</div>
        <div class="wordmark__sub">MAKRZ LLC</div>
        <div class="wordmark__sub">HAWAII</div>
      </div>
    </div>
    <div class="brand-rule"></div>
    <h1 class="person">DALE VORSKIN</h1>
    <div class="person-rule"></div>
    <div class="contact">
      <span class="contact__item">
        <svg class="icon" viewBox="0 0 24 24" aria-hidden="true"><path d="M6.6 10.8a15 15 0 0 0 6.6 6.6l2.2-2.2c.3-.3.7-.4 1-.2 1.1.4 2.3.6 3.6.6.6 0 1 .4 1 1V20c0 .6-.4 1-1 1A17 17 0 0 1 3 4c0-.6.4-1 1-1h3.5c.6 0 1 .4 1 1 0 1.3.2 2.5.6 3.6.1.3 0 .7-.2 1z"/></svg>
        555- 714-9082
      </span>
      <span class="contact__item">
        <svg class="icon" viewBox="0 0 24 24" aria-hidden="true"><path d="M3 5h18v14H3zm2 2v.5l7 4.5 7-4.5V7l-7 4.5z"/></svg>
        <span class="contact__email">OFFICE@TRV-GROUNDMAKRZ.COM</span>
      </span>
    </div>
  </section>

</main>
</body>
</html>
```